Home Page for a Swiss based start up company, trading Natural & Health food ingredients (B2B)

I would like to create a home page for my new start up company (Veltrana Swiss AG), the main field of activity is the trading and marketing of Natural and Health food ingredients towards the functional Food and Food supplements industry. (B2B).
Target Market : Functional Food and Food Supplement Manufacturers (B2B) based in Switzerland and Europe
The values I would like to convey are :
- sourcing of natural and health ingredients, (example : natural plant extracts, Omega 3, plant proteins, natural vitamins, vegan food ingredients...etc)
- Health & Nutritional Health
- Eco-friendly and Sustainability
- High Quality Standard in term of products and logistic services
- Trust and reliability
- Flexibility & speed to market
-Technical advice for the development of new products

The site will be translated in 3 languages (German, French, English)
Number of web pages : 5 : Home, About us, Products, Our Services, Contact

See here below attached Logo file.

Here some link of websites which can be taken as benchmark or source of inspiration
- https://quorbelix.com
- https://www.dralvimo.com/

Target Market(s)

Manufacturers of Functional Foods and Food Supplements in Switzerland and Europe (B2B)

Industry/Entity Type

B2B Trading of Natural & Health Ingredients

Coding

Number of Pages Required

Font styles to use
Sans Serif

Colors
0054AA
0677BA
7BADD7
CADEEF
E8F1F8
0094D4
00A9DD
6FCCEA
C7EBF8
E9F6FB
00AB8E
00BBA5
67D7C9
C6EFE9
E9F9F6
59FF00
82FF00
B8FF75
E3FFCB
F4FFEA
FFF300
FFF600
FEFA6F
FFFEC7
FFFEE8
FFC000
F8CF3A
FAE287
FDF2CF
FEFAEE
F0912C
F2A743
F7CA91
FBE8D2
FDF5EE
EE7325
F08F49
F5BC92
FAE3D3
FDF4ED

Requirements
Must have
• inspiration towards nature, sustainability, vegan food, functional food & beverages, food supplements, nutritional health, low carbon footprint
Should not have
• animals, chemistry, food additives

```html
<!DOCTYPE html>
<html lang="en">
<head>
<meta charset="utf-8">
<title>Veltrana Swiss AG – Natural &amp; Health Food Ingredients</title>
<link href="https://fonts.googleapis.com/css2?family=Alegreya+SC:wght@700;800&family=Montserrat:wght@400;500;600;700&display=swap" rel="stylesheet">
<style>
:root{
  --green:#6a8a2c;
  --green-dark:#557320;
  --green-light:#8fb043;
  --ink:#2b2b2b;
  --muted:#555;
  --night:#1f2a26;
  --footer:#1d1d1d;
  --white:#fff;
  --heading:"Alegreya SC",Georgia,serif;
  --body:"Montserrat",Arial,sans-serif;
}
*{box-sizing:border-box;margin:0;padding:0}
html,body{width:1200px;height:4827px;overflow:hidden}
body{position:relative;font-family:var(--body);color:var(--ink);background:var(--white)}
.abs{position:absolute}
.backdrop{position:absolute;left:0;top:0;width:1200px;height:4827px;z-index:1;pointer-events:none}
.layer{z-index:2}
/* header */
.topbar{left:497px;top:0;width:531px;height:38px;background:var(--green);clip-path:polygon(0 0,100% 0,96% 100%,4% 100%);display:flex;align-items:center;justify-content:center;gap:26px;color:#fff;font-size:12px}
.topbar span{display:flex;align-items:center;gap:8px}
.topbar .socials{display:flex;gap:8px}
.topbar .socials i{width:22px;height:22px;border:1.5px solid rgba(255,255,255,.8);border-radius:50%;display:block}
.brand{left:109px;top:26px;font-family:var(--body);font-weight:600;font-size:29px;color:var(--green);letter-spacing:.3px;white-space:nowrap}
.nav{left:530px;top:56px;display:flex;gap:26px;font-size:12px;font-weight:500;text-transform:uppercase}
.nav a{color:var(--ink);text-decoration:none}
.nav a.active{color:var(--green);border-bottom:3px solid var(--green);padding-bottom:8px}
/* hero */
.hero{left:0;top:90px;width:1200px;height:660px;background:linear-gradient(180deg,#8a9a7a 0%,#c9c7a4 22%,#6f8a3a 45%,#4f7d1f 65%,#5f9628 100%)}
.hero-title{left:112px;top:262px;font-family:var(--heading);font-size:72px;color:#fff;line-height:1;white-space:nowrap}
.hero-sub{left:112px;top:338px;font-size:23px;color:#fff;line-height:29px;font-weight:500}
.pill{display:flex;align-items:center;justify-content:space-between;border-radius:30px;font-weight:600;font-size:15px;padding:0 6px 0 20px}
.pill i{width:33px;height:33px;border-radius:50%;display:flex;align-items:center;justify-content:center}
.pill.light{background:#fff;color:var(--ink)}
.pill.light i{background:var(--green-dark)}
.pill.green{background:var(--green);color:#fff}
.pill.green i{background:#fff}
.hero-btn{left:113px;top:413px;width:166px;height:45px}
.arrow{top:368px;width:34px;height:26px}
.dots{top:667px;display:flex;gap:24px;left:506px}
.dots b{display:block;width:46px;height:2px;background:rgba(255,255,255,.7)}
.dots b.on{height:4px;background:#fff;margin-top:-1px}
/* section heads */
.eyebrow{width:1200px;left:0;text-align:center;font-size:23px;letter-spacing:3px;color:var(--ink);font-weight:500}
.title{width:1200px;left:0;text-align:center;font-family:var(--heading);font-size:48px;color:var(--green);line-height:1}
/* target */
.target-card{top:960px;width:454px;height:384px;border-radius:6px;overflow:hidden;box-shadow:0 6px 14px rgba(0,0,0,.25)}
.target-card .label{position:absolute;left:0;right:0;bottom:28px;text-align:center;font-family:var(--heading);font-size:25px;color:#fff;letter-spacing:.5px}
/* about */
.about-frame{left:92px;top:1584px;width:343px;height:280px;border:2px solid rgba(255,255,255,.75);border-right:none;border-bottom:none;border-radius:4px}
.about-img{left:111px;top:1601px;width:474px;height:388px;border-radius:4px;background:linear-gradient(160deg,#bfe08a 0%,#5e9a2c 35%,#2f5a18 70%,#1c2e10 100%)}
.dotgrid{left:375px;top:1992px;width:235px;height:66px;background-image:radial-gradient(rgba(255,255,255,.75) 1.3px,transparent 1.6px);background-size:11px 11px}
.about-copy{left:619px;top:1612px;width:462px;color:#fff}
.about-title{font-family:var(--heading);font-size:40px;line-height:48px}
.about-lead{margin-top:6px;font-size:18px;line-height:30px}
.about-text{margin-top:8px;font-size:13.5px;line-height:25px;text-align:justify}
.about-btn{left:615px;top:1933px;width:165px;height:44px}
/* values */
.tile{width:225px;height:199px;overflow:hidden}
.tile:before{content:"";position:absolute;inset:9px;border:1.5px solid rgba(255,255,255,.85)}
.tile span{position:absolute;left:20px;right:20px;bottom:38px;text-align:center;color:#fff;font-size:13px;font-weight:500;line-height:18px}
/* contact */
.contact-title{top:3058px}
.contact-sub{left:0;width:1200px;top:3125px;text-align:center;color:#fff;font-size:20px;letter-spacing:.2px}
.field{background:#fff;border-radius:2px;display:flex;align-items:center;gap:12px;padding:0 16px;font-family:Georgia,serif;font-size:12px;color:#333;letter-spacing:.5px}
.field.area{align-items:flex-start;padding-top:14px}
.contact-btn{left:516px;top:3484px;width:167px;height:43px}
/* gallery */
.gallery-text{left:240px;width:720px;top:3840px;text-align:center;font-size:16px;line-height:28px;color:var(--muted)}
.shot{top:3932px;width:190px;height:186px;border-radius:4px}
.more-btn{left:516px;top:4138px;width:167px;height:43px;background:var(--night);color:#fff}
.more-btn i{background:#fff}
/* footer */
.forest{left:0;top:4238px;width:1200px;height:210px;background:linear-gradient(180deg,rgba(255,255,255,0) 0%,#c9c9c9 35%,#6b6b6b 70%,#1d1d1d 100%)}
.footer{left:0;top:4444px;width:1200px;height:383px;background:var(--footer)}
.f-brand{left:111px;top:4545px;width:270px;text-align:center;font-weight:600;font-size:24px;color:var(--green);white-space:nowrap}
.f-social{top:4620px;width:30px;height:30px;border:1.5px solid #ddd;border-radius:50%}
.f-head{top:4490px;font-family:var(--heading);font-size:17px;color:#fff;letter-spacing:.5px}
.f-links{left:403px;top:4553px;list-style:none;color:#fff;font-size:12px;line-height:24px}
.f-contact{left:587px;top:4553px;width:250px;color:#fff;font-size:12px;line-height:20px}
.f-contact div{display:flex;gap:10px;margin-bottom:8px}
.f-contact svg{flex:none;margin-top:3px}
.f-note{left:864px;top:4555px;width:230px;color:#fff;font-size:12px;line-height:20px}
.f-input{left:864px;top:4611px;width:223px;height:34px;background:#fff;border-radius:18px;display:flex;align-items:center;gap:8px;padding:0 14px;font-size:11px;color:#555}
.f-btn{left:864px;top:4665px;width:167px;height:42px}
.rule{left:111px;top:4763px;width:978px;height:1px;background:#555}
.copy{left:0;width:1200px;top:4786px;text-align:center;color:#fff;font-size:13px}
.to-top{left:1122px;top:4744px;width:44px;height:44px;border-radius:50%;background:var(--green);display:flex;align-items:center;justify-content:center}
</style>
</head>
<body>

<div class="abs hero" role="img" aria-label="Sunlit green meadow with trees and low sun in the background"></div>

<svg class="backdrop" viewBox="0 0 1200 4827" aria-hidden="true">
  <path d="M0,647 C300,770 700,745 1200,688 L1200,752 L0,752 Z" fill="#fff"/>
  <path d="M0,674 C320,778 720,752 1200,694" fill="none" stroke="#6a8a2c" stroke-width="3"/>
  <path d="M0,1462 C400,1512 800,1512 1200,1462 L1200,2078 C820,2175 380,2175 0,2078 Z" fill="#6a8a2c"/>
  <path d="M0,2092 C360,2195 800,2182 1200,2100" fill="none" stroke="#6a8a2c" stroke-width="3"/>
  <path d="M0,2934 C400,2980 800,2980 1200,2934 L1200,3578 C820,3685 380,3680 0,3578 Z" fill="#1f2a26"/>
  <path d="M0,3594 C380,3700 820,3690 1200,3606" fill="none" stroke="#6a8a2c" stroke-width="3"/>
</svg>

<header class="layer">
  <div class="abs layer topbar">
    <span><svg width="16" height="12" viewBox="0 0 16 12"><rect x=".5" y=".5" width="15" height="11" fill="none" stroke="#fff"/><path d="M1 1l7 6 7-6" fill="none" stroke="#fff"/></svg>info@veltranaswiss.ch</span>
    <span><svg width="13" height="13" viewBox="0 0 24 24"><path fill="#fff" d="M6.6 10.8a15 15 0 006.6 6.6l2.2-2.2a1 1 0 011-.25 11.4 11.4 0 003.6.6 1 1 0 011 1V20a1 1 0 01-1 1A17 17 0 013 4a1 1 0 011-1h3.5a1 1 0 011 1c0 1.25.2 2.45.6 3.6a1 1 0 01-.25 1z"/></svg>+1 (555)-314-0270</span>
    <span class="socials"><i></i><i></i></span>
  </div>
  <div class="abs layer brand">VELTRANA SWISS AG</div>
  <nav class="abs layer nav">
    <a class="active" href="#">Home</a><a href="#">About Us</a><a href="#">Our Values</a><a href="#">Our Services</a><a href="#">Blog</a><a href="#">News</a><a href="#">Contact</a>
  </nav>
</header>

<section class="layer">
  <h1 class="abs layer hero-title">VELTRANA SWISS AG</h1>
  <p class="abs layer hero-sub">Consectetur adipiscing elitsedo<br>eiusmod tempor</p>
  <a class="abs layer pill light hero-btn">Order Now! <i><svg width="14" height="12" viewBox="0 0 14 12"><path d="M1 6h11M8 2l4 4-4 4" fill="none" stroke="#fff" stroke-width="1.8"/></svg></i></a>
  <svg class="abs layer arrow" style="left:40px" viewBox="0 0 34 26"><path d="M32 13H3M13 3L3 13l10 10" fill="none" stroke="#fff" stroke-width="3"/></svg>
  <svg class="abs layer arrow" style="left:1126px" viewBox="0 0 34 26"><path d="M2 13h29M21 3l10 10-10 10" fill="none" stroke="#fff" stroke-width="3"/></svg>
  <div class="abs layer dots"><b></b><b class="on"></b><b></b></div>
</section>

<section class="layer">
  <p class="abs layer eyebrow" style="top:836px">TARGET</p>
  <h2 class="abs layer title" style="top:874px">Our Target Market</h2>
  <div class="abs layer target-card" style="left:111px;background:linear-gradient(180deg,#bfe39a 0%,#6fb046 40%,#2f5a1f 75%,#1c2a14 100%)" role="img" aria-label="Small glass globe resting on moss among ferns">
    <div class="label">Functional Food</div>
  </div>
  <div class="abs layer target-card" style="left:626px;background:linear-gradient(180deg,#8fc23e 0%,#5f9a24 45%,#33561a 80%,#1d2b12 100%)" role="img" aria-label="Aerial view of a dense green forest canopy">
    <div class="label">Food Supplement Manufacturers</div>
  </div>
</section>

<section class="layer">
  <div class="abs layer about-frame"></div>
  <div class="abs layer about-img" role="img" aria-label="Forest path with sunlight streaming through green trees"></div>
  <div class="abs layer dotgrid"></div>
  <div class="abs layer about-copy">
    <h2 class="about-title">About Us</h2>
    <p class="about-lead">Totamrem aperiamsa eaqusdeipssa quaeabillo inventore veritatis etquasi architecto vitae.</p>
    <p class="about-text">Oaerspiciatis unde omnis saeoiseiste natus error sit voluptatem accusantium doloremque laudantium, totam rem aperiam, eaque ipsa quae ab illo inventore veritatis et quasi architecto beatae vitae dicta sunt explicabo. Nemo enim ipsam voluptatem quia voluptas sit aspernatur aut odit aut fugit, sed quia consequuntur magni dolores eos qui ratione voluptatem sequi nesciunt. Neque porro quisquam est, qui dolorem ipsum</p>
  </div>
  <a class="abs layer pill light about-btn">Learn More <i><svg width="14" height="12" viewBox="0 0 14 12"><path d="M1 6h11M8 2l4 4-4 4" fill="none" stroke="#fff" stroke-width="1.8"/></svg></i></a>
</section>

<section class="layer">
  <p class="abs layer eyebrow" style="top:2259px">VALUES</p>
  <h2 class="abs layer title" style="top:2298px">The Values</h2>
  <div class="abs layer tile" style="left:111px;top:2409px;background:linear-gradient(160deg,#c95a2a,#7a8a3a 50%,#4a3a24)" role="img" aria-label="Fresh fruit and vegetables"><span>Health &amp; Nutritional<br>Health</span></div>
  <div class="abs layer tile" style="left:358px;top:2409px;background:linear-gradient(160deg,#a33a2a,#8a7a3a 50%,#4a3522)" role="img" aria-label="Natural grains, seeds and vegetables"><span>Sourcing of natural &amp;<br>health ingredients</span></div>
  <div class="abs layer tile" style="left:607px;top:2409px;background:linear-gradient(160deg,#9ec052,#4f7a2a 55%,#2a3a1a)" role="img" aria-label="Hand holding a glass globe on green background"><span>Eco-friendly &amp;<br>Sustainability</span></div>
  <div class="abs layer tile" style="left:855px;top:2409px;background:linear-gradient(180deg,#2c3e5a,#9a5a4a 55%,#3a2a2a)" role="img" aria-label="Cargo plane, ship and trucks for logistics"><span>High Quality Standard in<br>term of products &amp;<br>logistic services</span></div>
  <div class="abs layer tile" style="left:111px;top:2636px;background:linear-gradient(160deg,#8a7a66,#b89a72 50%,#4a3a2a)" role="img" aria-label="Parcel being handed over in a warehouse"><span>Trust and<br>reliability</span></div>
  <div class="abs layer tile" style="left:358px;top:2636px;background:linear-gradient(160deg,#4a5a7a,#a07a50 55%,#3a2f2a)" role="img" aria-label="Stacks of parcels on a conveyor"><span>Flexibility &amp; speed<br>to market</span></div>
  <div class="abs layer tile" style="left:607px;top:2636px;background:linear-gradient(160deg,#5a5a5a,#8a7a6a 50%,#2a2a2a)" role="img" aria-label="Two colleagues discussing in an office"><span>Technical advice for the<br>development of new<br>products</span></div>
  <div class="abs layer tile" style="left:855px;top:2636px;background:linear-gradient(160deg,#3a4a6a,#8a6a4a 55%,#2a2a2a)" role="img" aria-label="Warehouse aisle with shelves of goods"><span>Security of<br>supply</span></div>
</section>

<section class="layer">
  <h2 class="abs layer title contact-title" style="color:#fff">Contact Us</h2>
  <p class="abs layer contact-sub">PERSPICIATIS UNDE OMNIS ISTE NATUS ERROR SIT VOLUPTATEM ACCUSANTIUM DOLOREMQUE</p>
  <div class="abs layer field" style="left:234px;top:3187px;width:357px;height:42px"><svg width="12" height="13" viewBox="0 0 12 13"><circle cx="6" cy="3.5" r="3" fill="#6a8a2c"/><path d="M0 13c0-4 2.5-6 6-6s6 2 6 6z" fill="#6a8a2c"/></svg>FIRST NAME</div>
  <div class="abs layer field" style="left:608px;top:3187px;width:356px;height:42px"><svg width="12" height="13" viewBox="0 0 12 13"><circle cx="6" cy="3.5" r="3" fill="#6a8a2c"/><path d="M0 13c0-4 2.5-6 6-6s6 2 6 6z" fill="#6a8a2c"/></svg>LAST NAME</div>
  <div class="abs layer field" style="left:234px;top:3249px;width:357px;height:42px"><svg width="16" height="12" viewBox="0 0 16 12"><rect x=".5" y=".5" width="15" height="11" fill="none" stroke="#6a8a2c"/><path d="M1 1l7 6 7-6" fill="none" stroke="#6a8a2c"/></svg>EMAIL</div>
  <div class="abs layer field" style="left:608px;top:3249px;width:356px;height:42px"><svg width="13" height="13" viewBox="0 0 24 24"><path fill="#6a8a2c" d="M6.6 10.8a15 15 0 006.6 6.6l2.2-2.2a1 1 0 011-.25 11.4 11.4 0 003.6.6 1 1 0 011 1V20a1 1 0 01-1 1A17 17 0 013 4a1 1 0 011-1h3.5a1 1 0 011 1c0 1.25.2 2.45.6 3.6a1 1 0 01-.25 1z"/></svg>PHONE</div>
  <div class="abs layer field area" style="left:234px;top:3311px;width:730px;height:128px"><svg width="12" height="12" viewBox="0 0 12 12"><path d="M1 1l10 10" stroke="#6a8a2c" stroke-width="2"/></svg>ADDRESS</div>
  <a class="abs layer pill green contact-btn">Submit <i><svg width="14" height="12" viewBox="0 0 14 12"><path d="M1 6h11M8 2l4 4-4 4" fill="none" stroke="#1f2a26" stroke-width="1.8"/></svg></i></a>
</section>

<section class="layer">
  <p class="abs layer eyebrow" style="top:3741px">GALLERY</p>
  <h2 class="abs layer title" style="top:3778px">Our Gallery</h2>
  <p class="abs layer gallery-text">Perspiciat isunde omnis istenatus errorsit voluptatem accusantium doloremque laudantium totam remaperiameaque ipsaqu aeabillo</p>
  <div class="abs layer shot" style="left:0;background:linear-gradient(160deg,#e8f0b0,#6fa12e 45%,#2a4a18)" role="img" aria-label="Globe resting in sunlit grass"></div>
  <div class="abs layer shot" style="left:202px;background:linear-gradient(160deg,#d8ecd0,#9ccf6a 50%,#4a7a2a)" role="img" aria-label="Hand holding a glowing green sphere"></div>
  <div class="abs layer shot" style="left:405px;background:linear-gradient(180deg,#6a8a6a,#2f4a2a 50%,#1a2a18);box-shadow:0 0 0 2px #333" role="img" aria-label="Looking up at a forest canopy"></div>
  <div class="abs layer shot" style="left:606px;background:linear-gradient(160deg,#b0d07a,#7aa04a 50%,#c48a3a)" role="img" aria-label="Hand holding a glowing light bulb with green icons"></div>
  <div class="abs layer shot" style="left:808px;background:linear-gradient(180deg,#2a3a5a,#4a7aa0 45%,#6a4a3a)" role="img" aria-label="Hands holding the Earth with trees on top"></div>
  <div class="abs layer shot" style="left:1011px;background:linear-gradient(160deg,#4a4a4a,#8a6a5a 50%,#2a2a2a)" role="img" aria-label="Cupped hands holding a young seedling"></div>
  <a class="abs layer pill more-btn">View More <i><svg width="14" height="12" viewBox="0 0 14 12"><path d="M1 6h11M8 2l4 4-4 4" fill="none" stroke="#1f2a26" stroke-width="1.8"/></svg></i></a>
</section>

<div class="abs layer forest" role="img" aria-label="Silhouette of a pine forest skyline"></div>
<footer class="abs layer footer"></footer>
<div class="abs layer f-brand">VELTRANA SWISS AG</div>
<div class="abs layer f-social" style="left:195px"></div>
<div class="abs layer f-social" style="left:238px"></div>

<h3 class="abs layer f-head" style="left:403px">Quick Links</h3>
<ul class="abs layer f-links"><li>Home</li><li>About us</li><li>Our values</li><li>Our services</li><li>Blog</li><li>News</li><li>Contact</li></ul>

<h3 class="abs layer f-head" style="left:587px">Contact Us</h3>
<div class="abs layer f-contact">
  <div><svg width="11" height="14" viewBox="0 0 11 14"><path d="M5.5 0a5.5 5.5 0 015.5 5.5C11 9.5 5.5 14 5.5 14S0 9.5 0 5.5A5.5 5.5 0 015.5 0z" fill="#6a8a2c"/><circle cx="5.5" cy="5.5" r="2" fill="#1d1d1d"/></svg><span>28 Birchwood Lane, Fairmont<br>Ohio, 40215, USA</span></div>
  <div><svg width="13" height="13" viewBox="0 0 13 13"><circle cx="6.5" cy="6.5" r="5.8" fill="none" stroke="#6a8a2c"/><path d="M6.5 3v3.7l2.2 1.4" fill="none" stroke="#6a8a2c"/></svg><span>Monday – Friday: 7am to 5pm<br>Saturday: 8am to 3pm<br>Sunday: Closed</span></div>
  <div><svg width="13" height="13" viewBox="0 0 24 24"><path fill="#6a8a2c" d="M6.6 10.8a15 15 0 006.6 6.6l2.2-2.2a1 1 0 011-.25 11.4 11.4 0 003.6.6 1 1 0 011 1V20a1 1 0 01-1 1A17 17 0 013 4a1 1 0 011-1h3.5a1 1 0 011 1c0 1.25.2 2.45.6 3.6a1 1 0 01-.25 1z"/></svg><span>+1 (555)-314-0270</span></div>
  <div><svg width="14" height="11" viewBox="0 0 16 12"><rect x=".5" y=".5" width="15" height="11" fill="#6a8a2c"/><path d="M1 1l7 6 7-6" fill="none" stroke="#1d1d1d"/></svg><span>info@veltranaswiss.ch</span></div>
</div>

<h3 class="abs layer f-head" style="left:864px">Latest Updates</h3>
<p class="abs layer f-note">To get our latest updates enter your email to receive.</p>
<div class="abs layer f-input"><svg width="14" height="11" viewBox="0 0 16 12"><rect x=".5" y=".5" width="15" height="11" fill="#6a8a2c"/><path d="M1 1l7 6 7-6" fill="none" stroke="#fff"/></svg>Enter Your E-Mail</div>
<a class="abs layer pill green f-btn">Submit <i><svg width="14" height="12" viewBox="0 0 14 12"><path d="M1 6h11M8 2l4 4-4 4" fill="none" stroke="#1d1d1d" stroke-width="1.8"/></svg></i></a>

<div class="abs layer rule"></div>
<p class="abs layer copy">Copyright © 2022 | All Rights Reserved</p>
<div class="abs layer to-top"><svg width="14" height="14" viewBox="0 0 14 14"><path d="M2 9l5-5 5 5" fill="none" stroke="#fff" stroke-width="2"/></svg></div>

</body>
</html>
```